We want to design total new business card and logo for Kestrel Building Services Ltd

Our company name Kestrel Building Services Ltd. Design new logo and business card , need hi-end luxury style art for architecture and construction industry. The card should simple but stylish. Our business focus on CONNECT tradesman to construction company, help marketing construction company tender oversea projects, managing franchise in construction sector, delivery amazing services to our client, so Logo should show the CONNECTION IDEA, CONNECTING PEOPLE, LUXURY. Visit our website for more information: kestrelgroup.example.nz

Target Market(s)

Directors or managers

Industry/Entity Type

Construction Company

Contact Information for Business Card

Name, Title, Mobile, Email, Website

Font styles to use
Serif

Colors

Designer to choose colors to be used in the design.

Requirements
Must have
• Simple and luxury, connection icon
Nice to have
• Special materials, plastic card, look through,...
• Look new ideas.

```html
<!DOCTYPE html>
<html lang="en">
<head>
<meta charset="utf-8">
<title>Kestrel Building Services Ltd – Business Card</title>
<link rel="stylesheet" href="https://fonts.googleapis.com/css2?family=Lora:wght@400;500&display=swap">
<style>
  :root {
    --backdrop: #141414;
    --card: #1f1f1f;
    --card-edge: #2a2a2a;
    --brand-blue: #1c67c4;
    --brand-teal: #24b3a2;
    --ink: #f2f2f2;
    --ink-soft: #d8d8d8;
  }
  * { box-sizing: border-box; margin: 0; padding: 0; }
  html, body {
    width: 1200px; height: 900px; overflow: hidden;
    background: var(--backdrop);
    font-family: "Lora", serif;
  }
  .canvas {
    position: relative; width: 1200px; height: 900px;
    background: radial-gradient(ellipse at 60% 40%, #262626 0%, var(--backdrop) 70%);
  }
  .card {
    position: absolute; left: 250px; width: 700px; height: 400px;
    background: linear-gradient(135deg, var(--card) 0%, #262626 60%, var(--card) 100%);
    border: 1px solid var(--card-edge);
    box-shadow: 0 18px 40px rgba(0,0,0,.6);
  }
  .card--front { top: 40px; }
  .card--back { top: 470px; }

  .lockup { display: flex; flex-direction: column; align-items: center; }
  .lockup__mark {
    width: 86px; height: 86px; border-radius: 50%;
    background: var(--brand-blue); margin-bottom: 22px;
  }
  .lockup__name {
    color: var(--brand-teal); font-weight: 500; text-align: center;
    text-transform: uppercase; line-height: 1.3;
  }
  .card--front .lockup {
    position: absolute; inset: 0; justify-content: center;
  }
  .card--front .lockup__name { font-size: 26px; letter-spacing: 3px; }

  .card--back .lockup {
    position: absolute; left: 18px; top: 0; bottom: 0; width: 324px;
    justify-content: center;
  }
  .card--back .lockup__mark { width: 90px; height: 90px; }
  .card--back .lockup__name { font-size: 21px; letter-spacing: 1.5px; }

  .divider {
    position: absolute; left: 356px; top: 80px; width: 2px; height: 240px;
    background: var(--brand-blue);
  }
  .contact {
    position: absolute; left: 392px; top: 92px; color: var(--ink);
  }
  .contact__name {
    color: var(--brand-blue); font-size: 25px; font-weight: 500;
    text-transform: uppercase; letter-spacing: .5px; line-height: 1;
  }
  .contact__title { font-size: 15px; margin: 8px 0 18px; color: var(--ink-soft); }
  .contact__address { font-size: 15px; line-height: 1.45; margin-bottom: 12px; letter-spacing: .4px; }
  .contact__list { list-style: none; font-size: 15px; letter-spacing: .4px; }
  .contact__item { display: flex; align-items: center; gap: 10px; line-height: 1.7; }
  .contact__icon { width: 14px; height: 14px; flex: none; fill: none; stroke: var(--brand-blue); stroke-width: 1.6; }
</style>
</head>
<body>
<main class="canvas">
  <section class="card card--front" aria-label="Card front">
    <div class="lockup">
      <span class="lockup__mark" aria-hidden="true"></span>
      <p class="lockup__name">Kestrel Building<br>Services Ltd</p>
    </div>
  </section>

  <section class="card card--back" aria-label="Card back">
    <div class="lockup">
      <span class="lockup__mark" aria-hidden="true"></span>
      <p class="lockup__name">Kestrel Building<br>Services Ltd</p>
    </div>
    <span class="divider" aria-hidden="true"></span>
    <div class="contact">
      <h1 class="contact__name">Daniel Hartley</h1>
      <p class="contact__title">Director</p>
      <p class="contact__address">118 Harbour Lane<br>Fairview, NC 28000</p>
      <ul class="contact__list">
        <li class="contact__item">
          <svg class="contact__icon" viewBox="0 0 16 16" aria-hidden="true"><path d="M4 1.5l2.5 3-1.5 1.5c.8 2 2.5 3.7 4.5 4.5l1.5-1.5 3 2.5-1.5 2.5C7 14 2 9 1.5 3z"/></svg>
          +330 5550-0142
        </li>
        <li class="contact__item">
          <svg class="contact__icon" viewBox="0 0 16 16" aria-hidden="true"><rect x="4" y="1.5" width="8" height="4"/><rect x="1.5" y="5.5" width="13" height="6"/><rect x="4" y="9.5" width="8" height="5"/></svg>
          +330 5550-0143
        </li>
        <li class="contact__item">
          <svg class="contact__icon" viewBox="0 0 16 16" aria-hidden="true"><rect x="1.5" y="3.5" width="13" height="9"/><path d="M1.5 3.5L8 9l6.5-5.5"/></svg>
          info@kestrelbuilding.example
        </li>
        <li class="contact__item">
          <svg class="contact__icon" viewBox="0 0 16 16" aria-hidden="true"><circle cx="8" cy="8" r="6.5"/><ellipse cx="8" cy="8" rx="3" ry="6.5"/><path d="M1.5 8h13"/></svg>
          www.kestrelbuilding.example
        </li>
      </ul>
    </div>
  </section>
</main>
</body>
</html>
```